PWNF Traditional Business Card Project

Please see attached....just a simple business card... on attachment- please use the exact font, style, etc as the attached "Ned Farley Broughton" card... however, replace with the "Walter Augustin Pryde" text and address below the card.

```html
<!DOCTYPE html>
<html lang="en">
<head>
<meta charset="utf-8">
<title>PWNF Business Card — Walter Augustin Pryde</title>
<link href="https://fonts.googleapis.com/css2?family=Cormorant+SC:wght@600;700&family=Montserrat:wght@400;500&display=swap" rel="stylesheet">
<style>
  :root {
    --backdrop: #5e5e5e;
    --card-light: #f1f1f1;
    --card-dark: #252525;
    --ink: #1c1c1c;
    --ink-reverse: #d9d9d9;
    --shadow: rgba(0, 0, 0, 0.35);
  }
  * { margin: 0; padding: 0; box-sizing: border-box; }
  html, body {
    width: 1200px;
    height: 1016px;
    overflow: hidden;
    background: var(--backdrop);
  }
  .card {
    position: absolute;
    left: 323px;
    width: 582px;
    height: 328px;
    box-shadow: 0 6px 14px var(--shadow);
  }
  .card--front { top: 163px; background: var(--card-light); color: var(--ink); }
  .card--back  { top: 544px; background: var(--card-dark); color: var(--ink-reverse); }

  .serif-caps {
    font-family: "Cormorant SC", "Times New Roman", serif;
    font-weight: 700;
    letter-spacing: 0.04em;
    line-height: 1;
    white-space: nowrap;
  }
  .wide-caps {
    font-family: "Montserrat", Arial, sans-serif;
    font-weight: 400;
    text-transform: uppercase;
    line-height: 1;
    white-space: nowrap;
  }

  /* front */
  .firm { position: absolute; left: 35px; top: 38px; }
  .firm__name { font-size: 24px; }
  .firm__sub { font-size: 9px; letter-spacing: 0.28em; margin-top: 4px; }

  .person {
    position: absolute;
    left: 0; right: 0;
    top: 142px;
    text-align: center;
  }
  .person__name { font-size: 30px; }
  .person__title { font-size: 9.5px; letter-spacing: 0.28em; margin-top: 4px; }

  .contact {
    position: absolute;
    top: 249px;
    font-family: "Montserrat", Arial, sans-serif;
    font-size: 12px;
    line-height: 17.5px;
    letter-spacing: 0.06em;
  }
  .contact--address { left: 36px; }
  .contact--lines { right: 35px; text-align: right; }
  .contact .lower { text-transform: none; letter-spacing: 0.01em; }

  /* back */
  .brand {
    position: absolute;
    left: 0; right: 0;
    top: 141px;
    text-align: center;
  }
  .brand__name { font-size: 29px; font-weight: 600; }
  .brand__sub { font-size: 10px; letter-spacing: 0.3em; margin-top: 6px; }
</style>
</head>
<body>
  <section class="card card--front" aria-label="Business card front">
    <div class="firm">
      <div class="firm__name serif-caps">Pacific Western</div>
      <div class="firm__sub wide-caps">Northfield Firm, PLC</div>
    </div>

    <div class="person">
      <div class="person__name serif-caps">Walter Augustin Pryde</div>
      <div class="person__title wide-caps">Attorney at Law</div>
    </div>

    <div class="contact contact--address">
      <div class="wide-caps">2470 Alder Street, Suite B</div>
      <div class="wide-caps">Larkmont, CA 91900</div>
      <div class="lower">www.lawpwnf.com</div>
    </div>

    <div class="contact contact--lines">
      <div class="wide-caps">Tel (555) 214-3390</div>
      <div class="wide-caps">Fax (555) 214-3391</div>
      <div class="lower">wpryde@lawpwnf.com</div>
    </div>
  </section>

  <section class="card card--back" aria-label="Business card back">
    <div class="brand">
      <div class="brand__name serif-caps">Pacific Western</div>
      <div class="brand__sub wide-caps">Northfield Firm, PLC</div>
    </div>
  </section>
</body>
</html>
```